Plate of the Raven: Half-Page Magazine Ad

advertisement in a travel magazine for a casual/fine dining restaurant in the heart of Whitehorse, Yukon
Needs to say that it is located in the Stonefield Hotel, 247 Larch Avenue.

Northern inspired cuisine
plateoftheraven.example

Don't need to use all the pictures

Dimensions: ad is a half-page, dimensions are 7.25" x 4.8".

Target Market(s)

Upscale dining, corporate travellers

Industry/Entity Type

Restaurant

Colors
0054AA
0677BA
7BADD7
CADEEF
E8F1F8
0094D4
00A9DD
6FCCEA
C7EBF8
E9F6FB
00AB8E
00BBA5
67D7C9
C6EFE9
E9F9F6

Requirements
Must have
• Restaurant logo
Nice to have
• Simple, clean design with upscale feel

```html
<!DOCTYPE html>
<html lang="en">
<head>
<meta charset="utf-8">
<title>Plate of the Raven – Half-Page Magazine Ad</title>
<link rel="stylesheet" href="https://fonts.googleapis.com/css2?family=Libre+Bodoni:wght@400;700&family=Mr+Dafoe&display=swap">
<style>
  :root {
    --canvas: #ffffff;
    --navy: #0054aa;
    --blue: #0677ba;
    --sky: #7badd7;
    --mist: #cadeef;
    --ice: #e8f1f8;
    --cyan: #00a9dd;
    --aqua: #6fccea;
    --teal: #00ab8e;
    --teal-light: #00bba5;
    --food-orange: #d8742a;
    --food-deep: #7a3412;
    --food-green: #3f8a3a;
    --panel: rgba(0, 84, 170, 0.80);
    --caption: rgba(0, 171, 142, 0.92);
    --ink-light: #ffffff;
    --accent: #c7ebf8;
    --badge: #ffffff;
    --badge-ink: #0054aa;
    --frame: rgba(255, 255, 255, 0.92);
  }
  * { box-sizing: border-box; margin: 0; padding: 0; }
  html, body {
    width: 1200px; height: 1200px; overflow: hidden;
    background: var(--canvas);
  }
  .ad-page {
    position: absolute; left: 50px; top: 236px;
    width: 1100px; height: 728px; overflow: hidden;
    font-family: "Libre Bodoni", "Times New Roman", serif;
    color: var(--ink-light);
    background: var(--navy);
  }
  .hero-photo {
    position: absolute; inset: 0;
    background:
      radial-gradient(ellipse 30% 35% at 62% 38%, rgba(63,138,58,0.95), rgba(63,138,58,0) 70%),
      radial-gradient(ellipse 20% 22% at 85% 65%, rgba(240,228,210,0.55), rgba(240,228,210,0) 70%),
      radial-gradient(ellipse 75% 80% at 55% 70%, var(--food-orange), var(--food-deep) 90%);
  }
  .hero-photo::after {
    content: ""; position: absolute; inset: 0;
    background: linear-gradient(90deg, rgba(0,84,170,0.55) 0%, rgba(0,84,170,0.15) 55%, rgba(0,84,170,0) 80%);
  }
  .edge-band {
    position: absolute; left: 0; right: 0; bottom: 0; height: 10px;
    background: linear-gradient(90deg, var(--navy), var(--blue), var(--cyan), var(--teal-light));
  }
  .logo-tag {
    position: absolute; right: 40px; top: 0; width: 190px; height: 160px;
  }
  .logo-tag svg { position: absolute; inset: 0; }
  .logo-tag__name {
    position: absolute; left: 18px; top: 26px; width: 160px;
    display: flex; align-items: center; gap: 12px;
    font-weight: 700; font-size: 18px; line-height: 1.1;
    color: var(--badge-ink); text-transform: uppercase;
  }
  .logo-tag__dot {
    flex: none; width: 36px; height: 36px; border-radius: 50%;
    background: var(--teal);
  }
  .headline {
    position: absolute; left: 60px; top: 58px; width: 620px;
    font-family: "Mr Dafoe", cursive;
    font-weight: 400; font-size: 50px; line-height: 52px;
    color: var(--ink-light);
  }
  .info-panel {
    position: absolute; left: 70px; top: 252px; width: 580px; height: 410px;
    background: var(--panel); border-radius: 14px;
    transform: rotate(-1deg);
  }
  .info-frame {
    position: absolute; left: 56px; top: 262px; width: 580px; height: 410px;
    border: 2px solid var(--frame); border-radius: 14px;
    transform: rotate(-3deg);
  }
  .info-copy {
    position: absolute; left: 108px; top: 284px; width: 510px;
    font-size: 13.5px; line-height: 20px;
  }
  .info-copy p + p { margin-top: 16px; }
  .info-copy .accent { color: var(--accent); font-weight: 700; }
  .patio-photo {
    position: absolute; left: 770px; top: 330px; width: 230px; height: 270px;
    border-radius: 14px;
    background: linear-gradient(160deg, #9fb2c8 0%, #6f7b86 35%, #4d5660 60%, #8a6a9c 85%, #c76a8a 100%);
  }
  .patio-frame {
    position: absolute; left: 790px; top: 340px; width: 230px; height: 290px;
    border: 2px solid var(--frame); border-radius: 14px;
    transform: rotate(-3deg);
  }
  .patio-caption {
    position: absolute; left: 850px; top: 610px; width: 190px; height: 56px;
    background: var(--caption); border-radius: 12px;
    display: flex; align-items: center; justify-content: center;
    text-align: center; font-size: 13px; line-height: 17px; padding: 0 14px;
  }
</style>
</head>
<body>
  <main class="ad-page">
    <div class="hero-photo" role="img" aria-label="Close-up photo of a plated pasta dish with tomato sauce, microgreens and shaved cheese in a bowl"></div>

    <div class="logo-tag">
      <svg viewBox="0 0 190 160" width="190" height="160" aria-hidden="true">
        <polygon points="0,0 190,0 190,105 95,158 0,105" fill="var(--badge)"/>
      </svg>
      <div class="logo-tag__name">
        <span class="logo-tag__dot"></span>
        <span>Plate<br>of the<br>Raven</span>
      </div>
    </div>

    <h1 class="headline">Plate of the Raven:<br>Northern Delights in<br>Whitehorse, Yukon!</h1>

    <div class="info-panel"></div>
    <div class="info-frame"></div>
    <div class="info-copy">
      <p>Experience the culinary wonders of the North at Plate of the Raven. Located in the heart of Whitehorse, Yukon, inside the <span class="accent">Stonefield Hotel on 247 Larch Avenue</span>, our restaurant offers casual fine dining with a touch of Northern inspiration.</p>
      <p>Indulge in our carefully crafted menu, showcasing the flavors of the Yukon with locally sourced ingredients and innovative combinations. From our cozy interiors to the uniquely dining experience, every visit is a memorable culinary adventure.</p>
      <p>Join us on our summer patio, where you can savor your meal while immersing yourself in the picturesque surroundings. Open for evening dining, Plate of the Raven invites you to experience the taste of the North in an unforgettable setting.</p>
      <p>Visit <span class="accent">plateoftheraven.example</span> to learn more and make a reservation. Discover the essence of Northern cuisine at Plate of the Raven in Whitehorse, Yukon.</p>
    </div>

    <div class="patio-photo" role="img" aria-label="Photo of the hotel entrance with a patio and hanging flower baskets"></div>
    <div class="patio-frame"></div>
    <div class="patio-caption">Open evenings with a summer patio.</div>

    <div class="edge-band"></div>
  </main>
</body>
</html>
```